A design led business card for the construction industry

High-end business card to match logo. White logo on dark grey/off black to the front. Matching dark font on white to back, possibly with logo design again.

We offer construction and project management services to commercial and private clients in the UK. Projetcs range from newbuilds, conversion of listed buildings and refurbishments and extensions of existing homes. Our focus is on quality and attention to detail using the highest skills.

Contact Information for Business Card

Name; Dorian Keble BSc
Position; Project Manager
Mobile; 07962 408 175
Tel; 01632 960457
email; dorian@stonevale.co.uk
web; www.stonevale.co.uk
Address; Ashcombe on Wey, KX4 7PW

Colors

Designer to choose only greyscale colors for use in the design.

Requirements
Must have
• To include the below description of the business,

CONSTRUCTION - PROJECT MANAGEMENT
Nice to have
• The posibility of the top back of the card being used as a ruler. So will have a measurement to scale in mm or an architect scale of 1:50
Should not have
• Should not be portrait

```html
<!DOCTYPE html>
<html lang="en">
<head>
<meta charset="utf-8">
<title>Stonevale — Business Card</title>
<link href="https://fonts.googleapis.com/css2?family=Montserrat:wght@300;400;700&display=swap" rel="stylesheet">
<style>
  :root {
    --backdrop: #0b0b0b;
    --card: #1c1c1c;
    --band: #111111;
    --ink: #f2f2f2;
    --ink-soft: #c9c9c9;
    --rule: #8a8a8a;
  }
  html, body {
    margin: 0;
    padding: 0;
    width: 1200px;
    height: 820px;
    overflow: hidden;
    background: radial-gradient(ellipse at 50% 40%, #1a1a1a 0%, var(--backdrop) 70%);
    font-family: "Montserrat", Arial, sans-serif;
    color: var(--ink);
  }
  .canvas {
    position: relative;
    width: 1200px;
    height: 820px;
  }
  .card {
    position: absolute;
    top: 242px;
    width: 520px;
    height: 336px;
    background: var(--card);
    box-shadow: 0 18px 40px rgba(0,0,0,0.6);
    overflow: hidden;
    text-align: center;
  }
  .card--contact { left: 50px; }
  .card--brand { left: 630px; }

  /* contact side */
  .contact__band {
    height: 122px;
    background: var(--band);
    display: flex;
    align-items: center;
    justify-content: center;
  }
  .wordmark {
    font-weight: 300;
    letter-spacing: 0.55em;
    text-transform: uppercase;
    color: var(--ink);
    margin: 0;
  }
  .contact__band .wordmark {
    font-size: 34px;
    padding-left: 0.55em;
    padding-top: 40px;
  }
  .contact__name {
    margin: 14px 0 0;
    font-size: 19px;
    font-weight: 700;
    letter-spacing: 0.02em;
  }
  .contact__role {
    margin: 2px 0 0;
    font-size: 11px;
    font-weight: 400;
    letter-spacing: 0.08em;
    color: var(--ink-soft);
  }
  .contact__icons {
    display: flex;
    justify-content: center;
    gap: 6px;
    margin: 10px 0 8px;
  }
  .contact__icons svg { width: 28px; height: 28px; }
  .contact__lines {
    margin: 0;
    padding: 0;
    list-style: none;
    font-size: 12.5px;
    line-height: 1.32;
    letter-spacing: 0.03em;
  }
  .contact__rule {
    width: 180px;
    height: 1px;
    background: var(--rule);
    margin: 8px auto 10px;
    border: 0;
  }
  .contact__address {
    margin: 0;
    font-size: 12.5px;
    letter-spacing: 0.04em;
  }

  /* brand side */
  .brand__mark {
    width: 92px;
    height: 92px;
    border: 5px solid var(--ink);
    border-radius: 6px;
    box-sizing: border-box;
    margin: 52px auto 0;
  }
  .card--brand .wordmark {
    font-size: 34px;
    margin-top: 30px;
    padding-left: 0.55em;
  }
  .brand__tagline {
    margin: 22px 0 0;
    font-size: 12px;
    font-weight: 400;
    letter-spacing: 0.06em;
    color: var(--ink-soft);
  }
</style>
</head>
<body>
<main class="canvas">

  <section class="card card--contact" aria-label="Contact side">
    <header class="contact__band">
      <p class="wordmark">Stonevale</p>
    </header>
    <h1 class="contact__name">DORIAN KEBLE BSC</h1>
    <p class="contact__role">PROJECT MANAGER</p>

    <div class="contact__icons" aria-hidden="true">
      <svg viewBox="0 0 28 28"><rect x="1.5" y="1.5" width="25" height="25" rx="5" fill="none" stroke="#f2f2f2" stroke-width="2"/><rect x="10" y="7" width="8" height="14" rx="1.5" fill="none" stroke="#f2f2f2" stroke-width="1.6"/><line x1="13" y1="18.5" x2="15" y2="18.5" stroke="#f2f2f2" stroke-width="1.4"/></svg>
      <svg viewBox="0 0 28 28"><rect x="1.5" y="1.5" width="25" height="25" rx="5" fill="none" stroke="#f2f2f2" stroke-width="2"/><circle cx="14" cy="14" r="7.5" fill="none" stroke="#f2f2f2" stroke-width="1.6"/><path d="M11 10.5c0 3.5 3 6.5 6.5 6.5l1-1.5-2-1.2-1 .8c-1.2-.6-2.2-1.6-2.8-2.8l.8-1-1.2-2z" fill="#f2f2f2"/></svg>
      <svg viewBox="0 0 28 28"><rect x="1.5" y="1.5" width="25" height="25" rx="5" fill="none" stroke="#f2f2f2" stroke-width="2"/><rect x="7" y="9" width="14" height="10" fill="#f2f2f2"/><path d="M7 9l7 6 7-6" fill="none" stroke="#1c1c1c" stroke-width="1.4"/></svg>
      <svg viewBox="0 0 28 28"><rect x="1.5" y="1.5" width="25" height="25" rx="5" fill="none" stroke="#f2f2f2" stroke-width="2"/><circle cx="14" cy="14" r="7" fill="none" stroke="#f2f2f2" stroke-width="1.4"/><ellipse cx="14" cy="14" rx="3" ry="7" fill="none" stroke="#f2f2f2" stroke-width="1.2"/><line x1="7" y1="14" x2="21" y2="14" stroke="#f2f2f2" stroke-width="1.2"/></svg>
    </div>

    <ul class="contact__lines">
      <li>07962 408 175</li>
      <li>01632 960457</li>
      <li>DORIAN@STONEVALE.CO.UK</li>
      <li>WWW.STONEVALE.CO.UK</li>
    </ul>
    <hr class="contact__rule">
    <p class="contact__address">ASHCOMBE ON WEY, KX4 7PW</p>
  </section>

  <section class="card card--brand" aria-label="Brand side">
    <div class="brand__mark" aria-hidden="true"></div>
    <p class="wordmark">Stonevale</p>
    <p class="brand__tagline">CONSTRUCTION - PROJECT MANAGEMENT</p>
  </section>

</main>
</body>
</html>
```